Business Card Design Project - 2 sided

We need a business card design for a card having one business on each side (ie. two businesses on one card). Would like a design that incorporates logo, tagline and normal fields (name, position, address, phone).

Would also like an allowance for small font text along the bottom (text to be determined, but less than 50 characters).

NB. Attached logo for Harbor Quill has two variations - either can be used.

www.harborquill-example.com / www.velmaro-example.com

```html
<!DOCTYPE html>
<html lang="en">
<head>
<meta charset="utf-8">
<title>Harbor Quill / Velmaro – Business Card</title>
<link rel="stylesheet" href="https://fonts.googleapis.com/css2?family=Open+Sans:wght@400;600;700&display=swap">
<style>
  :root {
    --page-bg: #ecebe8;
    --card-bg: #ffffff;
    --band-green: #8dc63f;
    --navy: #3b3a7f;
    --seo-blue: #2a7fc0;
    --seo-grey: #6d6e70;
    --text-dark: #3a3a3a;
    --text-muted: #666666;
    --divider: #9a9a9a;
  }
  * { box-sizing: border-box; margin: 0; padding: 0; }
  html, body {
    width: 1200px; height: 487px; overflow: hidden;
    background: var(--page-bg);
    font-family: "Open Sans", Arial, sans-serif;
  }
  .canvas { position: relative; width: 1200px; height: 487px; }

  .card {
    position: absolute; top: 90px;
    width: 542px; height: 311px;
    background: var(--card-bg);
    border-radius: 14px;
    box-shadow: 0 2px 6px rgba(0,0,0,.18);
    overflow: hidden;
  }
  .card--harbor { left: 38px; }
  .card--velmaro { left: 619px; }

  .brand {
    position: absolute; left: 0; right: 0; top: 60px;
    display: flex; align-items: center; justify-content: center; gap: 12px;
  }
  .brand__dot { width: 34px; height: 34px; border-radius: 50%; }
  .brand__name { font-weight: 600; font-size: 34px; letter-spacing: .5px; }
  .card--harbor .brand__dot { background: var(--band-green); }
  .card--harbor .brand__name { color: var(--navy); }
  .card--velmaro .brand__dot { background: var(--band-green); }
  .card--velmaro .brand__name { color: var(--seo-blue); }

  .tagline {
    position: absolute; left: 0; right: 0; text-align: center;
  }
  .card--harbor .tagline {
    top: 141px; font-size: 11px; font-weight: 700; color: var(--navy);
  }
  .card--velmaro .tagline {
    top: 122px; font-size: 16px; font-weight: 600; color: #2c6e9e; letter-spacing: .6px;
  }

  .name-band {
    position: absolute; top: 183px; left: 0; width: 511px; height: 31px;
    background: var(--band-green);
    display: flex; align-items: center; justify-content: center;
    color: #fff;
  }
  .name-band__name { font-size: 16px; font-weight: 700; }
  .name-band__title { font-size: 13px; margin-left: 6px; }
  .band-square { position: absolute; top: 183px; left: 516px; width: 26px; height: 31px; }
  .card--harbor .band-square { background: var(--navy); }
  .card--velmaro .band-square { background: var(--seo-grey); }

  .contact {
    position: absolute; top: 232px; left: 42px;
    display: flex; font-size: 13px; color: var(--text-dark); line-height: 18.5px;
  }
  .contact__col { padding-right: 10px; }
  .contact__col + .contact__col { border-left: 1px solid var(--divider); padding-left: 10px; }
  .contact__row { display: flex; align-items: center; gap: 6px; white-space: nowrap; }
  .contact__row svg { width: 11px; height: 11px; flex: none; }
  .icon { fill: var(--band-green); }

  .fine-print {
    position: absolute; top: 277px; left: 0; right: 0; text-align: center;
    font-size: 10.5px; color: var(--text-muted); letter-spacing: .2px;
  }
</style>
</head>
<body>
<div class="canvas">

  <section class="card card--harbor" aria-label="Harbor Quill side">
    <div class="brand"><span class="brand__dot"></span><span class="brand__name">Harbor Quill</span></div>
    <p class="tagline">Website Translation and Localisation Specialist...</p>
    <div class="name-band"><span class="name-band__name">Your Name</span><span class="name-band__title">/ Title</span></div>
    <div class="band-square"></div>
    <div class="contact">
      <div class="contact__col">
        <div class="contact__row"><svg viewBox="0 0 12 12"><path class="icon" d="M2 1l2 0 1 3-1.4 1a6 6 0 0 0 3.4 3.4L8 7l3 1v2a1 1 0 0 1-1 1A9 9 0 0 1 1 2a1 1 0 0 1 1-1z"/></svg>123-456-7890</div>
        <div class="contact__row"><svg viewBox="0 0 12 12"><rect class="icon" x="3" y="0.5" width="6" height="11" rx="1"/><rect x="4" y="2" width="4" height="6" fill="#fff"/></svg>123-456-7890</div>
      </div>
      <div class="contact__col">
        <div class="contact__row"><svg viewBox="0 0 12 12"><rect class="icon" x="0.5" y="2" width="11" height="8" rx="1"/><path d="M1 3l5 4 5-4" stroke="#fff" fill="none"/></svg>name@website.com</div>
        <div class="contact__row"><svg viewBox="0 0 12 12"><circle class="icon" cx="6" cy="6" r="5.5"/><path d="M0.5 6h11M6 .5c-3 3-3 8 0 11M6 .5c3 3 3 8 0 11" stroke="#fff" stroke-width=".8" fill="none"/></svg>www.website.com</div>
      </div>
      <div class="contact__col">
        <div class="contact__row">Complex name, Street</div>
        <div class="contact__row">City, State, zip code</div>
      </div>
    </div>
    <p class="fine-print">xxxxxxxxxxxxxxxxxxxxxxxxxxxxxxxxxxxxxxxxxxxxxxxxxx</p>
  </section>

  <section class="card card--velmaro" aria-label="Velmaro side">
    <div class="brand"><span class="brand__dot"></span><span class="brand__name">Velmaro LLC</span></div>
    <p class="tagline">Professional SEO Services</p>
    <div class="name-band"><span class="name-band__name">Your Name</span><span class="name-band__title">/ Title</span></div>
    <div class="band-square"></div>
    <div class="contact">
      <div class="contact__col">
        <div class="contact__row"><svg viewBox="0 0 12 12"><path class="icon" d="M2 1l2 0 1 3-1.4 1a6 6 0 0 0 3.4 3.4L8 7l3 1v2a1 1 0 0 1-1 1A9 9 0 0 1 1 2a1 1 0 0 1 1-1z"/></svg>123-456-7890</div>
        <div class="contact__row"><svg viewBox="0 0 12 12"><rect class="icon" x="3" y="0.5" width="6" height="11" rx="1"/><rect x="4" y="2" width="4" height="6" fill="#fff"/></svg>123-456-7890</div>
      </div>
      <div class="contact__col">
        <div class="contact__row"><svg viewBox="0 0 12 12"><rect class="icon" x="0.5" y="2" width="11" height="8" rx="1"/><path d="M1 3l5 4 5-4" stroke="#fff" fill="none"/></svg>name@website.com</div>
        <div class="contact__row"><svg viewBox="0 0 12 12"><circle class="icon" cx="6" cy="6" r="5.5"/><path d="M0.5 6h11M6 .5c-3 3-3 8 0 11M6 .5c3 3 3 8 0 11" stroke="#fff" stroke-width=".8" fill="none"/></svg>www.website.com</div>
      </div>
      <div class="contact__col">
        <div class="contact__row">Complex name, Street</div>
        <div class="contact__row">City, State, zip code</div>
      </div>
    </div>
    <p class="fine-print">xxxxxxxxxxxxxxxxxxxxxxxxxxxxxxxxxxxxxxxxxxxxxxxxxx</p>
  </section>

</div>
</body>
</html>
```